Business Card Design Project - 2 sided

We need a business card design for a card having one business on each side (ie. two businesses on one card). Would like a design that incorporates logo, tagline and normal fields (name, position, address, phone).

Would also like an allowance for small font text along the bottom (text to be determined, but less than 50 characters).

NB. Attached logo for Harbor Quill has two variations - either can be used.

www.harborquill-example.com / www.velmaro-example.com

```html
<!DOCTYPE html>
<html lang="en">
<head>
<meta charset="utf-8">
<title>Harbor Quill / Velmaro – Business Card</title>
<link rel="stylesheet" href="https://fonts.googleapis.com/css2?family=Open+Sans:wght@400;600;700&display=swap">
<style>
  :root {
    --stage: #ecebe8;
    --card: #ffffff;
    --green: #8cc63f;
    --green-deep: #6fa534;
    --green-light: #a8d95e;
    --navy: #2e2f6e;
    --blue-rule: #4a6fa8;
    --blue-mark: #3d74b8;
    --ink: #4a4a4a;
    --ink-soft: #5c5c5c;
    --divider: #9a9a9a;
  }
  * { box-sizing: border-box; margin: 0; padding: 0; }
  html, body { width: 1200px; height: 402px; overflow: hidden; }
  body {
    background: var(--stage);
    font-family: "Open Sans", Arial, sans-serif;
    color: var(--ink);
    position: relative;
  }
  .card {
    position: absolute;
    top: 56px;
    width: 512px;
    height: 290px;
    background: var(--card);
    overflow: hidden;
    box-shadow: 0 2px 6px rgba(0,0,0,.18);
  }
  .card--harbor { left: 61px; }
  .card--velmaro { left: 626px; }

  .card__band {
    position: absolute; left: 0; top: 0; width: 100%; height: 64px;
    background: var(--green);
    border-bottom: 2px solid var(--blue-rule);
  }
  .card--velmaro .card__band {
    background: radial-gradient(ellipse at 22% 30%, var(--green-light) 0%, var(--green) 45%, var(--green-deep) 100%);
  }
  .card__tab { position: absolute; top: 0; left: 0; }

  .brand { position: absolute; text-align: center; }
  .brand__mark {
    position: absolute; border-radius: 50%;
  }
  .brand__name {
    font-family: "Open Sans", Arial, sans-serif;
    font-weight: 600; white-space: nowrap;
  }
  .brand__tagline { font-size: 10px; font-weight: 600; color: #333; white-space: nowrap; }

  .card--harbor .brand__mark {
    left: 230px; top: 30px; width: 50px; height: 50px;
    background: var(--navy);
  }
  .card--harbor .brand__name {
    position: absolute; left: 0; top: 105px; width: 512px;
    font-size: 24px; letter-spacing: 1px; color: var(--navy);
    text-transform: uppercase;
  }
  .card--harbor .brand__tagline {
    position: absolute; left: 0; top: 136px; width: 512px; text-align: center;
  }

  .card--velmaro .brand__mark {
    left: 118px; top: 28px; width: 62px; height: 62px;
    background: var(--green);
  }
  .card--velmaro .brand__name {
    position: absolute; left: 192px; top: 36px;
    font-size: 48px; line-height: 1; color: var(--blue-mark);
  }
  .card--velmaro .brand__tagline {
    position: absolute; left: 192px; top: 120px;
    font-size: 14px; font-weight: 400; letter-spacing: .5px; color: #3a3a3a;
  }

  .person {
    position: absolute; left: 0; top: 166px; width: 100%;
    text-align: center; font-size: 16px; color: var(--ink);
  }
  .person__name { font-weight: 700; }
  .person__title { font-size: 13px; }
  .person__rule {
    position: absolute; left: 110px; top: 199px; width: 292px; height: 1px;
    background: linear-gradient(90deg, transparent, var(--green), transparent);
  }

  .contact {
    position: absolute; left: 48px; top: 212px;
    display: flex; font-size: 12.5px; line-height: 18px; color: var(--ink-soft);
  }
  .contact__group { padding: 0 10px; }
  .contact__group + .contact__group { border-left: 1px solid var(--divider); }
  .contact__group:first-child { padding-left: 0; }
  .contact__row { display: flex; align-items: center; gap: 5px; white-space: nowrap; }
  .contact__row svg { flex: none; }

  .footnote-rule {
    position: absolute; left: 120px; top: 254px; width: 272px; height: 1px;
    background: linear-gradient(90deg, transparent, var(--green), transparent);
  }
  .footnote {
    position: absolute; left: 0; top: 260px; width: 100%;
    text-align: center; font-size: 10px; letter-spacing: .2px; color: #444;
  }
</style>
</head>
<body>

<section class="card card--harbor">
  <div class="card__band"></div>
  <svg class="card__tab" width="512" height="70" viewBox="0 0 512 70" aria-hidden="true">
    <path d="M176 66 C176 30 205 20 256 20 C307 20 336 30 336 66 Z" fill="#fff"/>
  </svg>
  <div class="brand">
    <span class="brand__mark"></span>
    <div class="brand__name">Harbor Quill</div>
    <div class="brand__tagline">Website Translation and Localisation Specialist...</div>
  </div>
  <div class="person"><span class="person__name">Your Name</span> <span class="person__title">/ Title</span></div>
  <div class="person__rule"></div>
  <div class="contact">
    <div class="contact__group">
      <div class="contact__row"><svg width="9" height="10" viewBox="0 0 10 10"><path d="M2 1 L4 1 L5 3 L3.8 4.2 Q5 6.5 6.2 6.2 L7 5 L9 6 L9 8 Q8 9.5 6 9 Q1.5 7 1 2 Z" fill="#8cc63f"/></svg>123-456-7890</div>
      <div class="contact__row"><svg width="9" height="11" viewBox="0 0 8 11"><rect x="1" y="0.5" width="6" height="10" rx="1.2" fill="#8cc63f"/><rect x="2" y="2" width="4" height="4" fill="#fff"/></svg>123-456-7890</div>
    </div>
    <div class="contact__group">
      <div class="contact__row"><svg width="10" height="9" viewBox="0 0 10 9"><rect x="0.5" y="1" width="9" height="7" fill="#8cc63f"/><path d="M0.5 1 L5 5 L9.5 1" stroke="#fff" fill="none"/></svg>name@website.com</div>
      <div class="contact__row"><svg width="10" height="10" viewBox="0 0 10 10"><circle cx="5" cy="5" r="4.5" fill="#8cc63f"/><path d="M0.5 5 H9.5 M5 0.5 Q2 5 5 9.5 M5 0.5 Q8 5 5 9.5" stroke="#fff" stroke-width=".7" fill="none"/></svg>www.website.com</div>
    </div>
    <div class="contact__group">
      <div class="contact__row">Complex name, Street</div>
      <div class="contact__row">City, State, zip code</div>
    </div>
  </div>
  <div class="footnote-rule"></div>
  <div class="footnote">xxxxxxxxxxxxxxxxxxxxxxxxxxxxxxxxxxxxxxxxxxxxxxxxxx</div>
</section>

<section class="card card--velmaro">
  <div class="card__band"></div>
  <svg class="card__tab" width="512" height="70" viewBox="0 0 512 70" aria-hidden="true">
    <path d="M92 66 C92 32 115 18 150 18 C185 18 208 32 208 66 Z" fill="#fff"/>
  </svg>
  <div class="brand">
    <span class="brand__mark"></span>
    <div class="brand__name">Velmaro</div>
    <div class="brand__tagline">Professional SEO Services</div>
  </div>
  <div class="person"><span class="person__name">Your Name</span> <span class="person__title">/ Title</span></div>
  <div class="person__rule"></div>
  <div class="contact">
    <div class="contact__group">
      <div class="contact__row"><svg width="9" height="10" viewBox="0 0 10 10"><path d="M2 1 L4 1 L5 3 L3.8 4.2 Q5 6.5 6.2 6.2 L7 5 L9 6 L9 8 Q8 9.5 6 9 Q1.5 7 1 2 Z" fill="#8cc63f"/></svg>123-456-7890</div>
      <div class="contact__row"><svg width="9" height="11" viewBox="0 0 8 11"><rect x="1" y="0.5" width="6" height="10" rx="1.2" fill="#8cc63f"/><rect x="2" y="2" width="4" height="4" fill="#fff"/></svg>123-456-7890</div>
    </div>
    <div class="contact__group">
      <div class="contact__row"><svg width="10" height="9" viewBox="0 0 10 9"><rect x="0.5" y="1" width="9" height="7" fill="#8cc63f"/><path d="M0.5 1 L5 5 L9.5 1" stroke="#fff" fill="none"/></svg>name@website.com</div>
      <div class="contact__row"><svg width="10" height="10" viewBox="0 0 10 10"><circle cx="5" cy="5" r="4.5" fill="#8cc63f"/><path d="M0.5 5 H9.5 M5 0.5 Q2 5 5 9.5 M5 0.5 Q8 5 5 9.5" stroke="#fff" stroke-width=".7" fill="none"/></svg>www.website.com</div>
    </div>
    <div class="contact__group">
      <div class="contact__row">Complex name, Street</div>
      <div class="contact__row">City, State, zip code</div>
    </div>
  </div>
  <div class="footnote-rule"></div>
  <div class="footnote">xxxxxxxxxxxxxxxxxxxxxxxxxxxxxxxxxxxxxxxxxxxxxxxxxx</div>
</section>

</body>
</html>
```